Tree Pruning Website

We need a website for a tree Arborist, pruning company called Maple Crest Canopy Works. We look after all types of trees, knock down trees and prune trees. Our target market is from domestic clients to government clients and everything in between.

We would like to see the use of our main colours which are orange and green

We are not looking forward in seeing a template that we have seen before but a unique template. We have designed 5 templates ourselves and we wish for the design community to take our designs to the next level.

We have also designed a template for things that **we are not** looking for (Version 4)

To make it fair for everyone, we are also not giving out any participation payments as we have had. One winner will take all of the payment!!!

I Have attached a image of the designs and a image of a tree.

We are just looking at the PSD file been developed. We have our own team who can slice the image up into a HTML format.

Target Market(s)

Everyone who needs to cut down a tree

Industry/Entity Type

Government

Requirements
Must have
• Logo on front page
A List of our services
jQuery slider on page
Phone Number on every page

```html
<!DOCTYPE html>
<html lang="en">
<head>
<meta charset="utf-8">
<title>Maple Crest Canopy Works</title>
<link href="https://fonts.googleapis.com/css2?family=Cabin+Condensed:wght@400;500;600;700&family=Arimo:wght@400&display=swap" rel="stylesheet">
<style>
:root{
  --header-top:#c08640;
  --header-bottom:#a76c2c;
  --page-glow:#ecb565;
  --page-edge:#c27a30;
  --nav-text:#fbf1df;
  --panel-silver:#dcdcdc;
  --panel-silver-dark:#b9b9b9;
  --gold-top:#f6d55e;
  --gold-bottom:#e2b33b;
  --sidebar-fill:rgba(120,78,30,.28);
  --sidebar-box:rgba(95,60,22,.35);
  --sidebar-text:#fff6e6;
  --green-light:#a9ef1c;
  --green-dark:#5fb40a;
  --ink:#2d1c08;
  --body-ink:#1c1308;
  --footer-bg:#3f2c11;
  --footer-text:#1f1407;
  --footer-soft:#d8c39a;
  --leaf:#8ed23c;
  --photo-main:#557a1c;
  --photo-one:#5b8523;
  --photo-two:#3f6f4a;
  --photo-three:#667f52;
}
*{box-sizing:border-box;margin:0;padding:0}
html,body{width:1200px;height:1107px;overflow:hidden}
body{position:relative;font-family:"Arimo",Arial,sans-serif;
  background:radial-gradient(ellipse 640px 420px at 600px 620px,var(--page-glow),var(--page-edge) 95%);}
.site-header{position:absolute;left:0;top:0;width:1200px;height:127px;
  background:linear-gradient(var(--header-top),var(--header-bottom));
  border-bottom:2px solid #d49a50;box-shadow:0 3px 8px rgba(80,40,0,.35)}
.brand{position:absolute;display:flex;align-items:center;gap:12px}
.brand-mark{width:70px;height:70px;border-radius:50%;background:var(--leaf);flex:none}
.brand-name{font-family:"Cabin Condensed",sans-serif;font-weight:600;font-size:29px;line-height:31px;color:#2f2f2f}
.site-header .brand{left:22px;top:26px}
.main-nav{position:absolute;top:50px;left:0;width:1200px;font-family:"Cabin Condensed",sans-serif;font-weight:500;font-size:27px;color:var(--nav-text)}
.main-nav a{position:absolute;color:inherit;text-decoration:none;white-space:nowrap;text-shadow:0 1px 2px rgba(0,0,0,.35)}
.main-nav a.current{border-bottom:2px solid var(--nav-text)}
.slider{position:absolute;left:49px;top:180px;width:760px;height:350px;border-radius:5px;
  background:linear-gradient(#f2f2f2,var(--panel-silver) 80%,var(--panel-silver-dark));
  box-shadow:0 6px 14px rgba(70,35,0,.45)}
.slide-main{position:absolute;left:10px;top:10px;width:614px;height:299px;border-radius:3px 0 0 3px;
  background:radial-gradient(ellipse at 40% 55%,#7fa92c,var(--photo-main) 70%)}
.thumbs{position:absolute;left:624px;top:10px;width:120px;height:299px;background:#fff}
.thumb{position:absolute;left:6px;width:114px}
.thumb-1{top:5px;height:99px;background:var(--photo-one)}
.thumb-2{top:109px;height:100px;background:var(--photo-two)}
.thumb-3{top:214px;height:82px;background:var(--photo-three)}
.dots{position:absolute;top:317px;left:348px;display:flex;gap:12px}
.dot{width:22px;height:22px;border-radius:50%;background:linear-gradient(#fafafa,#d5d5d5);border:1px solid #a3a3a3}
.dot.active{background:radial-gradient(circle at 40% 35%,#e0a84a,#9a6314);border-color:#7a4c0e}
.gallery-label{position:absolute;right:24px;top:320px;font-family:"Cabin Condensed",sans-serif;font-weight:600;font-size:18px;color:#555}
.sidebar{position:absolute;left:828px;top:180px;width:360px;height:347px;border-radius:4px;background:var(--sidebar-fill);box-shadow:0 4px 10px rgba(80,40,0,.25)}
.sidebar-title{height:46px;border-radius:4px 4px 0 0;background:linear-gradient(var(--gold-top),var(--gold-bottom));
  border:1px solid #c99a2a;font-family:"Cabin Condensed",sans-serif;font-weight:600;font-size:20px;color:#6a4510;text-align:center;line-height:44px}
.sidebar-body{position:absolute;left:11px;top:57px;width:338px;height:274px;background:var(--sidebar-box);border-radius:3px;
  padding:6px 8px;font-size:15.5px;line-height:21.3px;color:var(--sidebar-text)}
.btn-more{position:absolute;right:22px;bottom:26px;width:102px;height:38px;border-radius:4px;
  background:linear-gradient(var(--green-light),var(--green-dark));border:1px solid #4b8d08;
  font-family:"Cabin Condensed",sans-serif;font-weight:600;font-size:18px;color:#1e3303;text-align:center;line-height:36px;
  box-shadow:0 2px 4px rgba(0,0,0,.3)}
.intro{position:absolute;left:55px;top:569px;width:1105px;height:356px;background:rgba(255,225,160,.16);border-radius:3px}
.intro-lead{position:absolute;left:8px;top:6px;width:1095px;font-family:"Cabin Condensed",sans-serif;font-weight:500;font-size:25px;line-height:34px;color:var(--ink);white-space:nowrap}
.intro-lead strong{font-weight:700}
.intro-copy{position:absolute;left:11px;top:133px;width:1040px;font-size:15.5px;line-height:21px;color:var(--body-ink)}
.intro-copy p+p{margin-top:3px}
.site-footer{position:absolute;left:0;top:958px;width:1200px;height:149px;background:var(--footer-bg);border-top:2px solid #6a4a1c}
.footer-info{position:absolute;left:66px;top:24px;font-family:"Cabin Condensed",sans-serif;font-weight:600;font-size:19px;line-height:25.5px;color:var(--footer-text);text-transform:uppercase;white-space:nowrap}
.footer-divider{position:absolute;left:579px;top:10px;width:2px;height:128px;background:#1e1406}
.site-footer .brand{left:600px;top:32px}
.site-footer .brand-name{color:#d7d7d7}
.footer-note{position:absolute;left:858px;top:14px;width:334px;font-size:15.5px;line-height:19.5px;color:var(--footer-soft)}
</style>
</head>
<body>
<header class="site-header">
  <div class="brand"><span class="brand-mark"></span><span class="brand-name">Maple Crest<br>Canopy Works</span></div>
  <nav class="main-nav">
    <a class="current" style="left:407px">HOME</a>
    <a style="left:530px">ABOUT US</a>
    <a style="left:685px">OUR SERVICES</a>
    <a style="left:873px">GET A QUOTE</a>
    <a style="left:1051px">CONTACT US</a>
  </nav>
</header>

<section class="slider">
  <div class="slide-main" role="img" aria-label="Photo of a sunlit woodland path lined with trees"></div>
  <div class="thumbs">
    <div class="thumb thumb-1" role="img" aria-label="Photo of sun shining through forest trees"></div>
    <div class="thumb thumb-2" role="img" aria-label="Photo of a large tree in a park"></div>
    <div class="thumb thumb-3" role="img" aria-label="Photo of bare trees in a field"></div>
  </div>
  <div class="dots"><span class="dot active"></span><span class="dot"></span><span class="dot"></span><span class="dot"></span></div>
  <div class="gallery-label">Photo Gallery</div>
</section>

<aside class="sidebar">
  <div class="sidebar-title">Lorem Ipsum</div>
  <div class="sidebar-body">Lorem ipsum dolor sit amet, consectetur adipiscing elit. Morbi ut nisl purus, eget tristique turpis. Vestibulum ut tellus nisi. Donec sit amet lectus id turpis pulvinar sollicitudin et ac sapien. Vivamus nisi lorem, ornare sit amet iaculis quis, aliquet id sapien. Fusce quis libero ultrices tortor auctor consequat eu vitae est. Proin ac mattis augue. Integer lobortis porttitor augue non pellentesque.</div>
  <div class="btn-more">Read More</div>
</aside>

<main class="intro">
  <p class="intro-lead">Lorem Ipsum dolor sit amet, consectetur adipiscing elit. <strong>Morbi ut</strong> nisl purus, eget tristique turpis. Ut<br>tell us nisi. Donec sit amet lectus id turpis <strong>pulvinar</strong> sollicitudin et ac saplen. Vivamus nisi lorem, orn<br>sit amet <strong>iacullis quis</strong>, aliquet id saplen.</p>
  <div class="intro-copy">
    <p>Proin eget lorem sit amet ligula luctus pulvinar. Sed elementum neque ac ligula aliquam ultrices. Maecenas vitae nunc id metus pellentesque pellentesque eleifend sed erat. Integer dignissim accumsan ligula, vitae pharetra leo bibendum a. Integer mollis accumsan volutpat. Cras acl lobortis metus. Mauris et enim at leo venenatis sodales. Suspendisse vitae ipsum vel nisi tincidunt imperdiet. Integer non elit nunc, vel moles tie diam. Etiam egestas imperdiet odio, ac aliquet metus facilisis a. Cras molestie sagittis felis vel placerat. Mauris varius odio in massa iaculis quis bibendum quam pretium. Proin faucibus nisl eu ligula porta id pharetra magna porta. Nullam et turpis id erat sagittis pulvinar eu quis quam. Nunc porttitor leo hendrerit metus mollis lacinia.</p>
    <p>ras gravida fringilla feugiat. Ut sed rhoncus ipsum. Quisque non nibh lectus, nec sodales velit. Cras velit diam, dapibus interdum cursus sed, venenatis sit amet dolor. Aenean auctor purus non nibh adipiscing vitae ultrices est bibendum. Lorem ipsum dolor sit amet, consectetur adipiscing elit. Class aptent taciti sociosqu ad litora torquent per conubia nostra, per inceptos himenaeos. Aenean felis odio, vehicula ac cursus vel, rhoncus non mi. Nulla facilisi.</p>
  </div>
</main>

<footer class="site-footer">
  <div class="footer-info">Maple Crest Canopy Works (c) I All rights reserved I 2013<br>Contact us: 08 5550 0142<br>Fax: 08 5550 0199<br>47 Birchwood Lane, Fernvale, WA 6999</div>
  <div class="footer-divider"></div>
  <div class="brand"><span class="brand-mark"></span><span class="brand-name">Maple Crest<br>Canopy Works</span></div>
  <p class="footer-note">Sed tortor quam, vehicula ac dictum eu, aliquam ut mauris. Vestibulum tempus, urna et ele mentum convallis, justo lorem consectetur sem, sit amet accumsan lorem sapien eget velit. Phasellus adipiscing elit id felis eleifend eu vestibulum sapien cursus.</p>
</footer>
</body>
</html>
```